Halvern Studio Works New Business Card

I am opening a new division of my business. I am a high end interior designer, and the new business is writing specs for construction projects. It will be marketed to the VERY high end contractor, architects and realtors. The client will actually be the one who pays us and signs the agreement, but it will be the contractor, architect or realtor that will recommend us. I have attached my current card and our previous logo which is still used on some of our paperwork. I would like the new logo to be connected in some way to what we are currently using. We will need to have room on the card for a person's name. I'd like to omit the address as we might be moving the office soon. The web address is www.HalvernStudioWorks.com. For this design, please use my name, Marisol Thornbury.

Target Market(s)

High End Luxury Contractors, Realtors and Architects

Industry/Entity Type

Residential Construction

Contact Information for Business Card

Halvern Studio Works, Phone: 555-214-9087, www.HalvernStudioWorks.com , Marisol Thornbury

Font styles to use
Sans Serif

Colors
ec1f27

Requirements
Must have
• Some visual reference to my current card and logos. Use the colors submitted on the business card I attached.
Nice to have
• A visual reference to my current card and logos. Use the colors submitted on the card I attached.
Should not have
• A physical address

```html
<!DOCTYPE html>
<html lang="en">
<head>
<meta charset="utf-8">
<title>Halvern Studio Works — Business Card</title>
<link href="https://fonts.googleapis.com/css2?family=Open+Sans:wght@400;600;700&display=swap" rel="stylesheet">
<style>
  :root {
    --backdrop: #ece9e6;
    --card-white: #ffffff;
    --brand-rust: #8b3019;
    --ink-grey: #6f6f6f;
    --wordmark-grey: #8a8a8a;
    --rule-grey: #b5b5b5;
    --on-rust: #f6ece6;
  }
  html, body {
    margin: 0;
    padding: 0;
    overflow: hidden;
  }
  body {
    width: 1200px;
    height: 1000px;
    background: var(--backdrop);
    position: relative;
    font-family: "Open Sans", Arial, sans-serif;
  }
  .card {
    position: absolute;
    left: 265px;
    width: 665px;
    height: 397px;
    box-shadow: 0 3px 10px rgba(0,0,0,0.18);
  }
  .card--front { top: 73px; background: var(--card-white); }
  .card--back { top: 532px; background: var(--brand-rust); }

  /* Front: brand lockup */
  .lockup {
    position: absolute;
    left: 40px;
    top: 139px;
    width: 274px;
    text-align: center;
  }
  .lockup__square {
    display: block;
    width: 97px;
    height: 56px;
    margin: 0 auto 12px;
    background: var(--brand-rust);
  }
  .lockup__name {
    display: block;
    font-size: 19px;
    font-weight: 400;
    letter-spacing: 1.2px;
    text-transform: uppercase;
    color: var(--wordmark-grey);
    line-height: 28px;
    white-space: nowrap;
  }
  .lockup__rule {
    height: 1px;
    background: var(--rule-grey);
    margin: 3px 0 4px;
  }
  .lockup__tagline {
    font-size: 10px;
    letter-spacing: 2.4px;
    text-transform: uppercase;
    color: var(--wordmark-grey);
    white-space: nowrap;
  }

  /* Front: contact block */
  .contact {
    position: absolute;
    left: 365px;
    top: 133px;
  }
  .contact__name {
    margin: 0 0 34px;
    font-size: 18px;
    font-weight: 700;
    color: var(--brand-rust);
    text-transform: uppercase;
    letter-spacing: 0.2px;
  }
  .contact__list {
    list-style: none;
    margin: 0;
    padding: 0;
  }
  .contact__item {
    display: flex;
    align-items: center;
    gap: 7px;
    font-size: 16px;
    color: var(--ink-grey);
    line-height: 24px;
    white-space: nowrap;
  }
  .contact__icon {
    width: 15px;
    height: 13px;
    fill: var(--brand-rust);
    flex: none;
  }

  /* Back */
  .back-lockup {
    position: absolute;
    left: 0;
    right: 0;
    top: 167px;
    text-align: center;
  }
  .back-lockup__inner {
    display: inline-block;
  }
  .back-lockup__name {
    display: block;
    font-size: 28px;
    font-weight: 400;
    letter-spacing: 2px;
    text-transform: uppercase;
    color: var(--on-rust);
    line-height: 40px;
    white-space: nowrap;
  }
  .back-lockup__rule {
    height: 1px;
    background: var(--on-rust);
    opacity: 0.7;
    margin: 4px 0 6px;
  }
  .back-lockup__tagline {
    font-size: 14px;
    letter-spacing: 3.3px;
    text-transform: uppercase;
    color: var(--on-rust);
    white-space: nowrap;
  }
</style>
</head>
<body>

<section class="card card--front" aria-label="Business card front">
  <div class="lockup">
    <span class="lockup__square"></span>
    <span class="lockup__name">Halvern Studio Works</span>
    <div class="lockup__rule"></div>
    <div class="lockup__tagline">Commercial | Residential Design</div>
  </div>

  <div class="contact">
    <h1 class="contact__name">Marisol Thornbury</h1>
    <ul class="contact__list">
      <li class="contact__item">
        <svg class="contact__icon" viewBox="0 0 15 13" aria-hidden="true">
          <path d="M1 4 C1 1 14 1 14 4 L14 5 L10.5 5 L10.5 3.5 L4.5 3.5 L4.5 5 L1 5 Z"/>
          <path d="M3 6 L12 6 L14 12 L1 12 Z"/>
        </svg>
        555.214.9087
      </li>
      <li class="contact__item">
        <svg class="contact__icon" viewBox="0 0 15 13" aria-hidden="true">
          <path d="M1 3 L14 3 L14 11 L1 11 Z M1.8 3.6 L7.5 7.8 L13.2 3.6 Z" fill-rule="evenodd"/>
        </svg>
        marisol@halvernstudioworks.com
      </li>
      <li class="contact__item">
        <svg class="contact__icon" viewBox="0 0 15 13" aria-hidden="true">
          <path d="M1 1 L14 1 L14 10 L1 10 Z M2.5 2.5 L2.5 8.5 L12.5 8.5 L12.5 2.5 Z" fill-rule="evenodd"/>
          <path d="M5 11 L10 11 L10 12.5 L5 12.5 Z"/>
        </svg>
        www.HalvernStudioWorks.com
      </li>
    </ul>
  </div>
</section>

<section class="card card--back" aria-label="Business card back">
  <div class="back-lockup">
    <div class="back-lockup__inner">
      <span class="back-lockup__name">Halvern Studio Works</span>
      <div class="back-lockup__rule"></div>
      <div class="back-lockup__tagline">Commercial | Residential Design</div>
    </div>
  </div>
</section>

</body>
</html>
```